Commercial, Public Works, Contractor needs a modern web design

We are a General and Engineering contracting firm with vast experience in our industry. Our focus is on Commercial, Tenant Improvement, Restaurants, and Public Works. We are opening a new business and would like that excitement and energy to show through the new web design. The colors we like are black, red and grey, we are open to color ideas. Attached is our logo design.

Industry/Entity Type

Restaurant

```html
<!DOCTYPE html>
<html lang="en">
<head>
<meta charset="utf-8">
<title>R.K. Holloway, Inc — General Engineering Contracting</title>
<link rel="stylesheet" href="https://fonts.googleapis.com/css2?family=Open+Sans:wght@400;600;700&display=swap">
<style>
:root{
  --red:#b5121b;
  --red-dark:#8e0d14;
  --ink:#333333;
  --muted:#777777;
  --light:#f2f2f2;
  --line:#dddddd;
  --band:#4a4a4a;
  --white:#ffffff;
}
*{box-sizing:border-box;margin:0;padding:0}
html,body{width:796px;height:1200px;overflow:hidden}
body{font-family:"Open Sans",Arial,sans-serif;color:var(--ink);background:var(--white);font-size:8px;line-height:1.45}

.site-header{height:42px;display:flex;align-items:center;justify-content:space-between;padding:0 22px 0 18px;border-bottom:1px solid var(--line)}
.brand{font-weight:600;font-size:14px;color:var(--ink)}
.main-nav{display:flex;align-items:center;gap:4px}
.main-nav a{font-size:7.5px;font-weight:600;color:var(--ink);text-decoration:none;padding:6px 10px;border:1px solid transparent}
.main-nav a.is-active{color:var(--red);border-color:var(--red)}
.search-box{margin-left:8px;width:62px;height:18px;border:1px solid var(--line);font-size:6.5px;color:var(--muted);padding:3px 5px;position:relative}
.search-box svg{position:absolute;right:4px;top:4px}

.hero{position:relative;height:342px;background:linear-gradient(120deg,#7e8a94 0%,#b9c2c8 35%,#d8dde0 60%,#9aa6ae 100%)}
.hero-title{position:absolute;left:292px;top:58px;color:var(--white);font-size:21px;font-weight:400;line-height:1.15}
.hero-arrow{position:absolute;top:156px;width:12px;height:18px;background:#111;display:flex;align-items:center;justify-content:center}
.hero-arrow.prev{left:0}.hero-arrow.next{right:0}
.hero-dots{position:absolute;left:50%;bottom:8px;transform:translateX(-50%);display:flex;gap:4px}
.hero-dots span{width:6px;height:6px;border-radius:50%;background:rgba(255,255,255,.6)}
.hero-dots span.on{background:var(--white)}

.services{display:grid;grid-template-columns:repeat(4,1fr);padding:24px 40px 20px;border-bottom:1px solid var(--line);height:311px}
.service{text-align:center;padding:0 22px;border-right:1px solid var(--line)}
.service:last-child{border-right:none}
.service-icon{width:46px;height:46px;border-radius:50%;background:var(--red);margin:0 auto 12px;display:flex;align-items:center;justify-content:center}
.service h3{color:var(--red);font-size:12px;font-weight:600;margin-bottom:8px}
.service p{font-size:7px;color:var(--muted);height:46px}
.btn{display:inline-block;background:#222;color:var(--white);font-size:6.5px;font-weight:700;padding:5px 9px;text-decoration:none;letter-spacing:.3px}

.welcome{margin:12px 38px 0;background:var(--light);border:1px solid var(--line);padding:16px 26px 18px;text-align:center;height:190px}
.welcome h2{font-size:12px;font-weight:600;margin-bottom:10px}
.welcome p{font-size:7px;color:var(--muted);margin-bottom:9px;text-align:left}

.testimonials{margin-top:14px;background:var(--band);height:136px;color:var(--white);text-align:center;padding-top:10px;position:relative}
.testimonials h2{font-size:12px;font-weight:600;margin-bottom:8px}
.quotes{display:grid;grid-template-columns:repeat(3,1fr);padding:0 60px;gap:30px}
.quote-icon{width:28px;height:28px;border-radius:50%;background:var(--white);margin:0 auto 6px;display:flex;align-items:center;justify-content:center}
.quote p{font-size:6.8px;color:#ddd;height:36px}
.quote cite{font-style:normal;font-weight:700;font-size:7px;letter-spacing:.3px}
.t-arrow{position:absolute;top:64px;font-size:12px;color:#bbb}
.t-arrow.prev{left:18px}.t-arrow.next{right:18px}

.site-footer{background:var(--red);height:153px;text-align:center;color:var(--white);padding-top:26px;position:relative}
.site-footer h4{font-size:8px;font-weight:400;margin-bottom:6px}
.social{display:flex;gap:4px;justify-content:center;margin-bottom:12px}
.social span{width:12px;height:12px;background:var(--white);opacity:.85}
.footer-nav{font-size:7px;margin-bottom:6px}
.footer-nav a{color:var(--white);text-decoration:none;margin:0 3px}
.copyright{font-size:6.5px;opacity:.9}
.footer-bar{position:absolute;left:0;right:0;bottom:0;height:22px;background:var(--red-dark);font-size:6.5px;line-height:22px}
</style>
</head>
<body>
<header class="site-header">
  <div class="brand">R.K. Holloway, Inc</div>
  <nav class="main-nav">
    <a class="is-active" href="#">HOME</a><a href="#">ABOUT</a><a href="#">SERVICES</a><a href="#">BLOG</a><a href="#">NEWS</a><a href="#">CONTACT</a>
    <div class="search-box">Search<svg width="8" height="8" viewBox="0 0 8 8"><circle cx="3.3" cy="3.3" r="2.4" fill="none" stroke="#777" stroke-width="1"/><line x1="5" y1="5" x2="7.5" y2="7.5" stroke="#777" stroke-width="1"/></svg></div>
  </nav>
</header>

<section class="hero" role="img" aria-label="Photo of two people shaking hands in business attire">
  <h1 class="hero-title">General Engineering<br>Contracting Firm</h1>
  <span class="hero-arrow prev"><svg width="6" height="8" viewBox="0 0 6 8"><path d="M5 0 1 4l4 4" fill="none" stroke="#fff" stroke-width="1.5"/></svg></span>
  <span class="hero-arrow next"><svg width="6" height="8" viewBox="0 0 6 8"><path d="M1 0l4 4-4 4" fill="none" stroke="#fff" stroke-width="1.5"/></svg></span>
  <div class="hero-dots"><span class="on"></span><span></span><span></span><span></span></div>
</section>

<section class="services">
  <article class="service">
    <div class="service-icon"><svg width="22" height="22" viewBox="0 0 22 22"><rect x="4" y="3" width="14" height="17" fill="#fff"/><g fill="#b5121b"><rect x="7" y="6" width="3" height="3"/><rect x="12" y="6" width="3" height="3"/><rect x="7" y="11" width="3" height="3"/><rect x="12" y="11" width="3" height="3"/><rect x="9.5" y="16" width="3" height="4"/></g></svg></div>
    <h3>Commercial</h3>
    <p>Contrary to popular belief, Lorem Ipsum is not simply random text. It has roots in a piece of classical Latin literature.</p>
    <a class="btn" href="#">READ MORE</a>
  </article>
  <article class="service">
    <div class="service-icon"><svg width="22" height="22" viewBox="0 0 22 22"><path d="M4 18 14 8" stroke="#fff" stroke-width="3" stroke-linecap="round"/><circle cx="16" cy="6" r="3.5" fill="none" stroke="#fff" stroke-width="2"/></svg></div>
    <h3>Tenant Improvement</h3>
    <p>It is a long established fact that a reader will be distracted by the readable content of a page when looking at its layout.</p>
    <a class="btn" href="#">READ MORE</a>
  </article>
  <article class="service">
    <div class="service-icon"><svg width="22" height="22" viewBox="0 0 22 22"><g stroke="#fff" stroke-width="2" stroke-linecap="round" fill="none"><path d="M7 3v16M5 3v5a2 2 0 0 0 4 0V3"/><path d="M15 19V3c2 1 3 4 3 7h-3"/></g></svg></div>
    <h3>Restaurants</h3>
    <p>There are many variations of passages of Lorem Ipsum available, but the majority have suffered alteration.</p>
    <a class="btn" href="#">READ MORE</a>
  </article>
  <article class="service">
    <div class="service-icon"><svg width="22" height="22" viewBox="0 0 22 22"><path d="M3 8 11 3l8 5z" fill="#fff"/><g fill="#fff"><rect x="5" y="9" width="2" height="8"/><rect x="10" y="9" width="2" height="8"/><rect x="15" y="9" width="2" height="8"/><rect x="3" y="18" width="16" height="2"/></g></svg></div>
    <h3>Public Works</h3>
    <p>The standard chunk of Lorem Ipsum used since the 1500s is reproduced below for those interested.</p>
    <a class="btn" href="#">READ MORE</a>
  </article>
</section>

<section class="welcome">
  <h2>Welcome to R.K. Holloway, Inc</h2>
  <p>Contrary to popular belief, Lorem Ipsum is not simply random text. It has roots in a piece of classical Latin literature from 45 BC, making it over 2000 years old. A Latin professor looked up one of the more obscure Latin words, consectetur, from a Lorem Ipsum passage, and going through the cites of the word in classical literature, discovered the undoubtable source.</p>
  <p>Scholars looked up one of the more obscure Latin words, consectetur, from a Lorem Ipsum passage, and going through the cites of the word in classical literature. The chunk of Lorem Ipsum used since the 1500s is reproduced below.</p>
  <a class="btn" href="#">READ MORE</a>
</section>

<section class="testimonials">
  <h2>Testimonials</h2>
  <span class="t-arrow prev">&#8249;</span><span class="t-arrow next">&#8250;</span>
  <div class="quotes">
    <blockquote class="quote">
      <div class="quote-icon"><svg width="12" height="10" viewBox="0 0 12 10"><path d="M0 10V5C0 2 2 0 5 0v2C3 2 2.5 3.5 2.5 5H5v5zm7 0V5c0-3 2-5 5-5v2c-2 0-2.5 1.5-2.5 3H12v5z" fill="#4a4a4a"/></svg></div>
      <p>Lorem Ipsum is simply dummy text of the printing and typesetting industry. Lorem Ipsum has been the industry's standard dummy text ever since the 1500s.</p>
      <cite>DANIEL ORTIZ</cite>
    </blockquote>
    <blockquote class="quote">
      <div class="quote-icon"><svg width="12" height="10" viewBox="0 0 12 10"><path d="M0 10V5C0 2 2 0 5 0v2C3 2 2.5 3.5 2.5 5H5v5zm7 0V5c0-3 2-5 5-5v2c-2 0-2.5 1.5-2.5 3H12v5z" fill="#4a4a4a"/></svg></div>
      <p>Contrary to popular belief, Lorem Ipsum is not simply random text. It has roots in a piece of classical Latin literature from 45 BC, making it over 2000 years old.</p>
      <cite>MARK ELLISON</cite>
    </blockquote>
    <blockquote class="quote">
      <div class="quote-icon"><svg width="12" height="10" viewBox="0 0 12 10"><path d="M0 10V5C0 2 2 0 5 0v2C3 2 2.5 3.5 2.5 5H5v5zm7 0V5c0-3 2-5 5-5v2c-2 0-2.5 1.5-2.5 3H12v5z" fill="#4a4a4a"/></svg></div>
      <p>There are many variations of passages of Lorem Ipsum available, but the majority have suffered alteration in some form, by injected humour or randomised text.</p>
      <cite>PETER LANG</cite>
    </blockquote>
  </div>
</section>

<footer class="site-footer">
  <h4>Connect with us</h4>
  <div class="social"><span></span><span></span><span></span><span></span></div>
  <nav class="footer-nav"><a href="#">Home</a>| <a href="#">About Us</a>| <a href="#">Services</a>| <a href="#">Blog</a>| <a href="#">News</a>| <a href="#">Contact Us</a></nav>
  <div class="copyright">Copyright © 2015 All Rights Reserved</div>
  <div class="footer-bar">42 Harlow Avenue | Brookfield | 555-0170</div>
</footer>
</body>
</html>
```